independent cleaner, reliable, custom, thorough, trustworthy

Not sure yet if I want single-sided or double sided, so I'm selecting double-sided just in case, but single-sided designs are okay.

Really looking to find the happy medium between personal and professional in a business card design. I end up building comfortable relationships with the people I work for.

Most of my business is through referrals, but I want some business cards to hand out to people who ask for one (and maybe put them on community bulletin boards).

My target market is homeowners and business owners who are looking for a reliable cleaner and are willing to pay a bit more to have excellent quality and someone they trust.

Theme: I have a personal-professional feel since I'm solo, so the theme should reflect that. Trustworthy, personal, simple. I clean up messes.

Hopefully this is enough info, let me know if you have any questions though of course!

Target Market(s)

Homeowners businessowners who are looking for a reliable cleaner, excellent quality trustworthy.

Industry/Entity Type

Cleaning Service

Contact Information for Business Card

Please include this text:
• Delphine Marwood
• independent cleaner
• reliable, custom, thorough
• 604-315-2970
• tbh.marwood@quellmail.com

Font styles to use
Serif
Sans Serif

Colors
ffffff
00a990
0492cd
33a6d7
0355a3
3276b5
919191

Requirements
Must have
• Really looking to find the happy medium between personal and professional in a business card design.
• Background: at least 50% white on the side with the most text (coloured accents or shapes are okay)
• I lean more towards simple and clean, solid colours, maybe a gentle gradient
Nice to have
• Not sure yet if I want single-sided or double sided, so I'm selecting double-sided just in case, but single-sided designs are okay.
• Colours: preferably blues and teals for the font and other objects (if any). Open to designer's choice though. I've toyed around with orangey-yellow, but it doesn't feel right and I keep going back to blues/teals
• Also I uploaded a sketch of my signature and initials so you can get a feel for my personality. I'm not expecting this to be included in the design, it's just there.
Should not have
• I don't like a lot of busy-ness or textures
• Also I don't have a logo (not sure where else to specify this)

```html
<!DOCTYPE html>
<html lang="en">
<head>
<meta charset="utf-8">
<title>Delphine Marwood – Independent Cleaner</title>
<link href="https://fonts.googleapis.com/css2?family=Cinzel:wght@400;600&family=Lato:wght@300;400&display=swap" rel="stylesheet">
<style>
  :root {
    --white: #ffffff;
    --teal: #00a990;
    --blue: #0492cd;
    --blue-light: #33a6d7;
    --grey: #919191;
    --ink: #3a3a3a;
    --ghost: #efefef;
    --backdrop: #d9d9d9;
  }
  * { margin: 0; padding: 0; box-sizing: border-box; }
  html, body { width: 1200px; height: 900px; overflow: hidden; }
  body {
    background: var(--backdrop);
    position: relative;
    font-family: "Lato", sans-serif;
  }
  .card {
    position: absolute;
    width: 520px;
    height: 300px;
    border-radius: 22px;
    overflow: hidden;
  }

  /* Front side */
  .card-front {
    left: 90px;
    top: 130px;
    background: linear-gradient(120deg, var(--blue) 0 64%, var(--teal) 64% 100%);
    display: flex;
    align-items: center;
    justify-content: center;
  }
  .front-name {
    font-family: "Cinzel", serif;
    font-weight: 600;
    font-size: 36px;
    letter-spacing: 2px;
    color: var(--white);
  }

  /* Back side */
  .card-back {
    left: 600px;
    top: 470px;
    background: var(--white);
  }
  .ghost-name {
    position: absolute;
    right: 24px;
    top: 26px;
    font-family: "Cinzel", serif;
    font-weight: 600;
    font-size: 44px;
    line-height: 1.05;
    text-align: right;
    color: var(--ghost);
  }
  .brand {
    position: absolute;
    left: 30px;
    top: 92px;
    display: flex;
    align-items: center;
    gap: 14px;
  }
  .brand-mark {
    display: flex;
    align-items: center;
    gap: 8px;
  }
  .brand-square {
    width: 14px;
    height: 14px;
    background: var(--teal);
  }
  .brand-mark-name {
    font-family: "Cinzel", serif;
    font-weight: 600;
    font-size: 11px;
    color: var(--blue);
    width: 66px;
    line-height: 1.2;
  }
  .identity { position: relative; }
  .holder-name {
    font-family: "Cinzel", serif;
    font-weight: 600;
    font-size: 25px;
    letter-spacing: 1px;
    line-height: 1;
  }
  .holder-name .first { color: var(--blue); }
  .holder-name .last { color: var(--teal); }
  .holder-role {
    margin-top: 4px;
    font-size: 11.5px;
    letter-spacing: 4.4px;
    text-transform: uppercase;
    color: var(--grey);
    font-weight: 400;
  }
  .contact {
    position: absolute;
    left: 30px;
    bottom: 34px;
    list-style: none;
  }
  .contact li {
    display: flex;
    align-items: center;
    gap: 8px;
    font-size: 23px;
    font-weight: 300;
    color: var(--ink);
    line-height: 1.4;
  }
  .contact svg { width: 22px; height: 18px; flex: none; }
</style>
</head>
<body>

  <section class="card card-front" aria-label="Card front">
    <span class="front-name">Delphine Marwood</span>
  </section>

  <section class="card card-back" aria-label="Card back">
    <div class="ghost-name" aria-hidden="true">Delphine<br>Marwood</div>

    <div class="brand">
      <div class="brand-mark">
        <span class="brand-square"></span>
        <span class="brand-mark-name">Delphine Marwood</span>
      </div>
      <div class="identity">
        <h1 class="holder-name"><span class="first">Delphine</span> <span class="last">Marwood</span></h1>
        <p class="holder-role">Independent Cleaner</p>
      </div>
    </div>

    <ul class="contact">
      <li>
        <svg viewBox="0 0 22 18" aria-hidden="true">
          <path d="M2 7 Q11 -1 20 7 L17 9 L15 6 Q11 4 7 6 L5 9 Z" fill="var(--blue)"/>
          <path d="M6 9 L16 9 L19 17 L3 17 Z" fill="var(--blue)"/>
          <circle cx="11" cy="13" r="2" fill="var(--white)"/>
        </svg>
        604-315-2970
      </li>
      <li>
        <svg viewBox="0 0 22 18" aria-hidden="true">
          <rect x="1" y="2" width="20" height="14" fill="var(--blue)"/>
          <path d="M1 2 L11 10 L21 2" fill="none" stroke="var(--white)" stroke-width="1.6"/>
        </svg>
        tbh.marwood@quellmail.com
      </li>
    </ul>
  </section>

</body>
</html>
```